Business Management Fortress

Assist with enhancing a powerpoint slide by providing a few design options for consideration. I have a template but open to any creative ideas.

Internal employees and stakeholders

Business Management, Finance, Accounting

• Maintain a fortress, temple, or pyramid schema
• Scenic Background

```html
<!DOCTYPE html>
<html lang="en">
<head>
<meta charset="utf-8">
<title>Business Management Fortress</title>
<link rel="stylesheet" href="https://fonts.googleapis.com/css2?family=Figtree:wght@400;600;700&display=swap">
<style>
  :root {
    --ink: #111114;
    --sky-top: #cfdde6;
    --sky-mid: #e3e4e1;
    --stone: #d8cfc4;
    --ground: #e9e2d9;
    --pink: #d4186c;
    --purple: #7a00e0;
    --blue: #006ed9;
    --cyan: #00d9dc;
    --green: #00d26a;
    --yellow: #ecc200;
    --body-light: #f6f6f9;
    --body-dark: #8c8a95;
  }
  * { margin: 0; padding: 0; box-sizing: border-box; }
  html, body { width: 1200px; height: 675px; overflow: hidden; }
  body { font-family: "Figtree", "Helvetica Neue", Arial, sans-serif; color: var(--ink); }
  .slide { position: relative; width: 1200px; height: 675px; overflow: hidden; }
  .scenic-backdrop {
    position: absolute; inset: 0;
    background:
      radial-gradient(ellipse 60% 45% at 50% 55%, rgba(200,188,172,0.55), transparent 70%),
      linear-gradient(180deg, var(--sky-top) 0%, var(--sky-mid) 35%, var(--stone) 65%, var(--ground) 100%);
  }
  .fortress-diagram { position: absolute; inset: 0; width: 1200px; height: 675px; }
  .tier-label { font-family: "Figtree", "Helvetica Neue", Arial, sans-serif; font-weight: 600; fill: var(--ink); letter-spacing: 0.5px; }
  .ring-label { font-family: "Figtree", "Helvetica Neue", Arial, sans-serif; font-weight: 600; fill: var(--ink); letter-spacing: 1px; }
  .crown-label { font-family: "Figtree", "Helvetica Neue", Arial, sans-serif; font-weight: 700; fill: #ffffff; letter-spacing: 2px; }
  .pillar { position: absolute; width: 170px; }
  .pillar-title { font-size: 13.75px; font-weight: 700; text-transform: uppercase; line-height: 18px; white-space: nowrap; }
  .pillar-text { margin-top: 4px; font-size: 11.2px; line-height: 18.75px; font-weight: 400; white-space: nowrap; }
  .page-code { position: absolute; right: 22px; top: 642px; font-size: 11px; font-weight: 700; }
</style>
</head>
<body>
<div class="slide">
  <div class="scenic-backdrop" role="img" aria-label="Soft scenic photograph of a hilltop stone castle beneath a pale sky"></div>

  <svg class="fortress-diagram" viewBox="0 0 1920 1080" xmlns="http://www.w3.org/2000/svg">
    <defs>
      <linearGradient id="cylinder-side" x1="0" x2="1" y1="0" y2="0">
        <stop offset="0" stop-color="var(--body-light)"/>
        <stop offset="0.45" stop-color="#e6e5ec"/>
        <stop offset="1" stop-color="var(--body-dark)"/>
      </linearGradient>
      <path id="arc-fiduciary" d="M773 427 A195 95 0 0 0 1163 427"/>
      <path id="arc-alliances" d="M843 409 A125 46 0 0 0 1093 409"/>
      <path id="arc-business" d="M823 357 A145 49 0 0 0 1113 357"/>
      <path id="arc-innovation" d="M888 308 A80 38 0 0 0 1048 308"/>
      <path id="arc-people" d="M908 264 A60 30 0 0 0 1028 264"/>
      <path id="arc-profit" d="M884 204 A85 33 0 0 0 1054 204"/>
      <path id="arc-leader" d="M909 161 A60 23 0 0 0 1029 161"/>
      <path id="arc-partner" d="M899 77 A70 37 0 0 0 1039 77"/>
    </defs>

    <g class="connectors" stroke="var(--ink)" stroke-width="3" fill="none">
      <line x1="478" y1="455" x2="722" y2="457"/>
      <line x1="1213" y1="461" x2="1428" y2="455"/>
      <line x1="678" y1="622" x2="800" y2="552"/>
      <line x1="877" y1="663" x2="921" y2="588"/>
      <line x1="1063" y1="663" x2="1018" y2="588"/>
      <line x1="1260" y1="620" x2="1140" y2="550"/>
    </g>

    <g class="fortress-core">
      <ellipse cx="968" cy="455" rx="245" ry="133" fill="none" stroke="var(--ink)" stroke-width="3"/>

      <path d="M761 350 L761 455 A207 118 0 0 0 1175 455 L1175 350 Z" fill="url(#cylinder-side)"/>
      <ellipse cx="968" cy="350" rx="207" ry="118" fill="var(--purple)"/>

      <path d="M811 270 L811 340 A157 90 0 0 0 1125 340 L1125 270 Z" fill="url(#cylinder-side)"/>
      <ellipse cx="968" cy="270" rx="157" ry="90" fill="var(--blue)"/>

      <path d="M849 180 L849 255 A120 65 0 0 0 1089 255 L1089 180 Z" fill="url(#cylinder-side)"/>
      <ellipse cx="969" cy="180" rx="120" ry="65" fill="var(--cyan)"/>

      <path d="M876 87 L876 160 A93 53 0 0 0 1062 160 L1062 87 Z" fill="url(#cylinder-side)"/>
      <ellipse cx="969" cy="87" rx="93" ry="53" fill="var(--green)"/>

      <text class="tier-label" font-size="27"><textPath href="#arc-fiduciary" startOffset="50%" text-anchor="middle">FIDUCIARY RESPONSIBILITIES</textPath></text>
      <text class="ring-label" font-size="18"><textPath href="#arc-alliances" startOffset="50%" text-anchor="middle">STRATEGIC  ALLIANCES</textPath></text>
      <text class="tier-label" font-size="23"><textPath href="#arc-business" startOffset="50%" text-anchor="middle">BUSINESS INTELLIGENCE</textPath></text>
      <text class="ring-label" font-size="18"><textPath href="#arc-innovation" startOffset="50%" text-anchor="middle">INNOVATION</textPath></text>
      <text class="tier-label" font-size="22"><textPath href="#arc-people" startOffset="50%" text-anchor="middle">PEOPLE</textPath></text>
      <text class="ring-label" font-size="17"><textPath href="#arc-profit" startOffset="50%" text-anchor="middle">PROFITABILITY</textPath></text>
      <text class="tier-label" font-size="22"><textPath href="#arc-leader" startOffset="50%" text-anchor="middle">LEADER</textPath></text>
      <text class="crown-label" font-size="27"><textPath href="#arc-partner" startOffset="50%" text-anchor="middle">PARTNER</textPath></text>
    </g>

    <g class="pod pod-cost">
      <ellipse cx="361" cy="453" rx="115" ry="62" fill="none" stroke="var(--ink)" stroke-width="3"/>
      <path d="M257 365 L257 440 A103 53 0 0 0 463 440 L463 365 Z" fill="url(#cylinder-side)"/>
      <ellipse cx="360" cy="365" rx="103" ry="53" fill="var(--pink)"/>
      <circle cx="361" cy="324" r="51" fill="#fff"/>
      <circle cx="361" cy="324" r="36" fill="none" stroke="var(--ink)" stroke-width="4" stroke-dasharray="14 6"/>
      <circle cx="361" cy="324" r="22" fill="none" stroke="var(--ink)" stroke-width="3.5"/>
      <text x="361" y="335" font-size="30" font-weight="700" text-anchor="middle" fill="var(--ink)">$</text>
    </g>

    <g class="pod pod-financials">
      <ellipse cx="575" cy="685" rx="115" ry="62" fill="none" stroke="var(--ink)" stroke-width="3"/>
      <path d="M472 595 L472 672 A103 53 0 0 0 678 672 L678 595 Z" fill="url(#cylinder-side)"/>
      <ellipse cx="575" cy="595" rx="103" ry="53" fill="var(--purple)"/>
      <g stroke="var(--ink)" stroke-width="3.5" fill="#fff" stroke-linejoin="round">
        <path d="M546 514 H605 V585 L595 595 H546 Z"/>
        <rect x="533" y="534" width="10" height="14"/>
        <rect x="550" y="526" width="10" height="22"/>
        <rect x="565" y="520" width="10" height="28"/>
        <line x1="554" y1="560" x2="596" y2="560"/>
        <line x1="570" y1="572" x2="596" y2="572"/>
        <line x1="570" y1="584" x2="590" y2="584"/>
        <path d="M553 581 L558 586 L566 576" fill="none"/>
      </g>
    </g>

    <g class="pod pod-controls">
      <ellipse cx="814" cy="797" rx="115" ry="62" fill="none" stroke="var(--ink)" stroke-width="3"/>
      <path d="M710 708 L710 785 A103 53 0 0 0 916 785 L916 708 Z" fill="url(#cylinder-side)"/>
      <ellipse cx="813" cy="708" rx="103" ry="53" fill="var(--blue)"/>
      <rect x="777" y="625" width="77" height="79" rx="18" fill="#fff" stroke="var(--ink)" stroke-width="3.5"/>
      <g stroke="var(--ink)" stroke-width="3.5" fill="#fff">
        <line x1="800" y1="640" x2="800" y2="690"/>
        <line x1="816" y1="640" x2="816" y2="690"/>
        <line x1="832" y1="640" x2="832" y2="690"/>
        <circle cx="800" cy="654" r="5"/>
        <circle cx="816" cy="677" r="5"/>
        <circle cx="832" cy="662" r="5"/>
      </g>
    </g>

    <g class="pod pod-brand">
      <ellipse cx="1125" cy="797" rx="115" ry="62" fill="none" stroke="var(--ink)" stroke-width="3"/>
      <path d="M1022 707 L1022 784 A103 53 0 0 0 1228 784 L1228 707 Z" fill="url(#cylinder-side)"/>
      <ellipse cx="1125" cy="707" rx="103" ry="53" fill="var(--cyan)"/>
      <g stroke="var(--ink)" stroke-width="3.5" fill="#fff" stroke-linejoin="round">
        <rect x="1096" y="640" width="70" height="60" rx="3"/>
        <path d="M1087 700 H1175 L1170 710 H1092 Z"/>
        <path d="M1131 630 L1150 638 V656 Q1150 672 1131 680 Q1112 672 1112 656 V638 Z"/>
        <path d="M1123 652 L1131 647 L1139 652 V662 L1131 667 L1123 662 Z" fill="none"/>
      </g>
    </g>

    <g class="pod pod-compliance">
      <ellipse cx="1364" cy="684" rx="115" ry="62" fill="none" stroke="var(--ink)" stroke-width="3"/>
      <path d="M1261 594 L1261 671 A103 53 0 0 0 1467 671 L1467 594 Z" fill="url(#cylinder-side)"/>
      <ellipse cx="1364" cy="594" rx="103" ry="53" fill="var(--green)"/>
      <g stroke="var(--ink)" stroke-width="3.5" fill="#fff" stroke-linejoin="round">
        <rect x="1335" y="515" width="62" height="76"/>
        <line x1="1347" y1="535" x2="1372" y2="535"/>
        <line x1="1347" y1="550" x2="1385" y2="550"/>
        <line x1="1347" y1="565" x2="1385" y2="565"/>
        <line x1="1347" y1="578" x2="1385" y2="578"/>
        <path d="M1392 505 L1412 513 V530 Q1412 545 1392 553 Q1372 545 1372 530 V513 Z"/>
        <path d="M1384 528 L1390 534 L1401 522" fill="none"/>
        <path d="M1332 572 V564 Q1332 554 1341 554 Q1350 554 1350 564 V572" fill="none"/>
        <rect x="1325" y="572" width="33" height="24" rx="2"/>
      </g>
    </g>

    <g class="pod pod-ethics">
      <ellipse cx="1544" cy="453" rx="115" ry="62" fill="none" stroke="var(--ink)" stroke-width="3"/>
      <path d="M1441 364 L1441 441 A103 53 0 0 0 1647 441 L1647 364 Z" fill="url(#cylinder-side)"/>
      <ellipse cx="1544" cy="364" rx="103" ry="53" fill="var(--yellow)"/>
      <g stroke="var(--ink)" stroke-width="3.5" fill="#fff" stroke-linejoin="round">
        <path d="M1550 310 Q1525 285 1513 315 Q1505 340 1550 372 Q1595 340 1587 315 Q1575 285 1550 310 Z"/>
        <path d="M1500 287 L1520 300 L1512 312 L1498 304 Z"/>
        <path d="M1600 287 L1580 300 L1588 312 L1602 304 Z"/>
        <rect x="1543" y="335" width="14" height="40" rx="6"/>
        <rect x="1540" y="374" width="22" height="10"/>
      </g>
    </g>
  </svg>

  <div class="pillar" style="left:107px; top:353px;">
    <h2 class="pillar-title">Cost Management</h2>
    <p class="pillar-text">Lorem ipsum dolor sit amet,<br>consectetur adipiscing elit, sed<br>do eiusmod tempor incididunt<br>ut labore et dolore</p>
  </div>
  <div class="pillar" style="left:200px; top:497px;">
    <h2 class="pillar-title">Accurate Financials</h2>
    <p class="pillar-text">Lorem ipsum dolor sit amet,<br>consectetur adipiscing elit, sed<br>do eiusmod tempor incididunt<br>ut labore et dolore</p>
  </div>
  <div class="pillar" style="left:400px; top:568px;">
    <h2 class="pillar-title">Internal Controls</h2>
    <p class="pillar-text">Lorem ipsum dolor sit amet,<br>consectetur adipiscing elit, sed<br>do eiusmod tempor incididunt<br>ut labore et dolore</p>
  </div>
  <div class="pillar" style="left:657px; top:567px;">
    <h2 class="pillar-title">Brand Protection</h2>
    <p class="pillar-text">Lorem ipsum dolor sit amet,<br>consectetur adipiscing elit, sed<br>do eiusmod tempor incididunt<br>ut labore et dolore</p>
  </div>
  <div class="pillar" style="left:857px; top:497px;">
    <h2 class="pillar-title">Compliance</h2>
    <p class="pillar-text">Lorem ipsum dolor sit amet,<br>consectetur adipiscing elit, sed<br>do eiusmod tempor incididunt<br>ut labore et dolore</p>
  </div>
  <div class="pillar" style="left:970px; top:353px;">
    <h2 class="pillar-title">Ethics</h2>
    <p class="pillar-text">Lorem ipsum dolor sit amet,<br>consectetur adipiscing elit, sed<br>do eiusmod tempor incididunt<br>ut labore et dolore</p>
  </div>

  <div class="page-code">C48</div>
</div>
</body>
</html>
```